Colin Vardek Business card

Hey there, I’m hoping to have a business card designed. I’m in Real estate and just switched to a new Brokerage called: The Harbourline Property Group

The back could just be the company name maybe or whatever looks good!

I’ve attached some logos of our company and some cards my buddy had done up.

On the card:
Colin Vardek
colinvardek@mailora.com
587-412-9065
colinvardek.ca

Target Market(s)

Home buyers and sellers

Industry/Entity Type

Real Estate

Contact Information for Business Card

just looking for a cool and modern design with my picture on it. I like the idea of Black and red being used.

Requirements
Must have
• all the details provided. I'm open to anything. Just want a professional looking card.

```html
<!DOCTYPE html>
<html lang="en">
<head>
<meta charset="utf-8">
<title>Colin Vardek – Business Card</title>
<link rel="stylesheet" href="https://fonts.googleapis.com/css2?family=Roboto:wght@400;500;700;900&display=swap">
<style>
  :root {
    --canvas-bg: #2b2a2d;
    --card-bg: #222127;
    --card-edge: #d3203a;
    --brand-red: #d3203a;
    --text-light: #ffffff;
    --photo-top: #3a3a40;
    --photo-bottom: #26252b;
    --pattern-tone: #1b1a1f;
  }
  * { box-sizing: border-box; margin: 0; padding: 0; }
  html, body { width: 1200px; height: 852px; overflow: hidden; }
  body {
    background: var(--canvas-bg);
    font-family: "Roboto", Arial, sans-serif;
    position: relative;
  }
  .card {
    position: absolute;
    width: 620px;
    height: 354px;
    border-radius: 26px;
    background: var(--card-bg);
    border-bottom: 5px solid var(--card-edge);
    border-left: 2px solid var(--card-edge);
    border-right: 2px solid var(--card-edge);
    overflow: hidden;
  }
  .card--back { left: 70px; top: 50px; }
  .card--front { left: 510px; top: 448px; }

  /* back */
  .back-pattern {
    position: absolute; inset: 0;
    background: var(--pattern-tone);
  }
  .back-brand {
    position: absolute;
    right: 48px; bottom: 70px;
    width: 210px;
    color: var(--text-light);
    font-weight: 900;
    font-size: 22px;
    line-height: 1.05;
    text-transform: uppercase;
    text-align: right;
  }

  /* front */
  .front-photo {
    position: absolute;
    right: 0; top: 0;
    width: 300px; height: 100%;
    background: linear-gradient(180deg, var(--photo-top), var(--photo-bottom));
  }
  .front-brand {
    position: absolute;
    left: 36px; top: 92px;
    width: 300px;
    color: var(--text-light);
    font-weight: 900;
    font-size: 34px;
    line-height: 1.02;
    text-transform: uppercase;
  }
  .front-accent {
    position: absolute;
    left: 0; top: 236px;
    width: 12px; height: 40px;
    background: var(--brand-red);
  }
  .agent-name {
    position: absolute;
    left: 36px; top: 232px;
    color: var(--brand-red);
    font-weight: 500;
    font-size: 26px;
  }
  .contact-list {
    position: absolute;
    left: 36px; top: 276px;
    list-style: none;
  }
  .contact-item {
    display: flex; align-items: center; gap: 8px;
    color: var(--text-light);
    font-size: 17px;
    line-height: 22px;
  }
  .contact-icon { width: 13px; height: 13px; flex: none; }
</style>
</head>
<body>

<section class="card card--back" aria-label="Card back">
  <div class="back-pattern" role="img" aria-label="Dark tonal repeat of the company name across the card"></div>
  <div class="back-brand">The Harbourline Property Group</div>
</section>

<section class="card card--front" aria-label="Card front">
  <div class="front-photo" role="img" aria-label="Portrait photo of Colin Vardek in a dark blazer and white shirt"></div>
  <div class="front-brand">The Harbourline Property Group</div>
  <div class="front-accent"></div>
  <h1 class="agent-name">Colin Vardek</h1>
  <ul class="contact-list">
    <li class="contact-item">
      <svg class="contact-icon" viewBox="0 0 24 24" fill="#d3203a"><path d="M6.6 10.8a15.1 15.1 0 0 0 6.6 6.6l2.2-2.2a1 1 0 0 1 1-.25 11.4 11.4 0 0 0 3.6.57 1 1 0 0 1 1 1V20a1 1 0 0 1-1 1A17 17 0 0 1 3 4a1 1 0 0 1 1-1h3.5a1 1 0 0 1 1 1c0 1.25.2 2.45.57 3.57a1 1 0 0 1-.25 1z"/></svg>
      587-412-9065
    </li>
    <li class="contact-item">
      <svg class="contact-icon" viewBox="0 0 24 24" fill="#d3203a"><path d="M2 5h20v14H2z"/><path d="M2 5l10 8 10-8" fill="none" stroke="#222127" stroke-width="2"/></svg>
      colinvardek@mailora.com
    </li>
    <li class="contact-item">
      <svg class="contact-icon" viewBox="0 0 24 24"><circle cx="12" cy="12" r="10" fill="#d3203a"/><path d="M2 12h20M12 2c3 3 3 17 0 20M12 2c-3 3-3 17 0 20" fill="none" stroke="#222127" stroke-width="1.6"/></svg>
      colinvardek.ca
    </li>
  </ul>
</section>

</body>
</html>
```